New Web Design Project

Number of Pages Required

1 page

Requirements
Must have
• An Overview / Background of the Business & Services(not for profit rescue animal farm)
• The Target Market / Audience you are trying to reach (animal lovers)
• Design Specifics; any preferences or ideas for Style, Colour, Imagery, etc (no preferences)

```html
<!DOCTYPE html>
<html lang="en">
<head>
<meta charset="utf-8">
<title>Cedar Hollow Farms</title>
<link href="https://fonts.googleapis.com/css2?family=Roboto:wght@400;500;700;900&display=swap" rel="stylesheet">
<style>
:root{
  --green:#3c9a1e;
  --green-dark:#2e7f14;
  --ink:#1d1d1d;
  --text:#555;
  --grey-bg:#eeeeef;
  --footer:#151515;
  --white:#fff;
  --hero-sky:#7f9bb5;
  --hero-grass:#5a8a2c;
}
*{box-sizing:border-box;margin:0;padding:0}
html,body{width:1200px;height:3939px;overflow:hidden}
body{font-family:"Roboto",sans-serif;color:var(--ink);background:var(--white);position:relative}
.abs{position:absolute}
.btn{display:inline-flex;align-items:center;gap:8px;background:var(--green);color:var(--white);font-weight:700;font-size:15px;text-transform:uppercase;height:46px;padding:0 24px;border-radius:2px;white-space:nowrap}
/* header / hero */
.hero-photo{left:0;top:0;width:1200px;height:700px;background:linear-gradient(180deg,#4d5a63 0%,var(--hero-sky) 18%,#6f8663 34%,#587e33 55%,var(--hero-grass) 80%,#4f7d25 100%)}
.brand{left:110px;top:48px;font-size:30px;font-weight:700;color:var(--white)}
.nav{left:522px;top:58px;width:406px;display:flex;justify-content:space-between;font-size:14px;font-weight:500;color:var(--white);white-space:nowrap}
.nav-donate{left:958px;top:46px;width:129px;height:42px;font-size:14px;padding:0;justify-content:center}
.hero-title{left:0;top:250px;width:1200px;text-align:center;font-size:56px;font-weight:700;color:var(--white)}
.hero-sub{left:270px;top:344px;width:660px;text-align:center;font-size:22px;font-weight:700;line-height:34px;color:var(--white)}
.hero-curve{left:0;top:560px}
.action{position:absolute;width:172px;height:172px;border-radius:50%;background:#e4e4e4;display:flex;align-items:center;justify-content:center}
.action-inner{width:144px;height:144px;border-radius:50%;background:var(--green);border:5px solid var(--white);display:flex;flex-direction:column;align-items:center;justify-content:center;gap:6px;color:var(--white);font-weight:700;font-size:22px}
/* about */
.about-title{left:110px;top:846px;font-size:40px;font-weight:700}
.about-text{left:110px;top:935px;width:460px;font-size:14px;line-height:23px;color:var(--text)}
.about-text p{margin-bottom:22px}
.about-btn{left:110px;top:1192px}
.video-frame{left:693px;top:900px;width:462px;height:337px;border:3px solid var(--green)}
.video{left:625px;top:856px;width:462px;height:316px;background:linear-gradient(180deg,#3a5a2c 0%,#5d8a3a 45%,#6fa33c 70%,#4a6e2a 100%)}
.play{left:824px;top:982px;width:64px;height:64px;border-radius:50%;background:rgba(0,0,0,.45);border:2px solid var(--white)}
/* help */
.help{left:0;top:1339px;width:1200px;height:644px;background:var(--grey-bg)}
.help-title{left:0;top:1508px;width:1200px;text-align:center;font-size:40px;font-weight:700}
.card{top:1610px;width:294px;height:268px;background:var(--white);text-align:center;padding-top:32px;box-shadow:0 2px 6px rgba(0,0,0,.06)}
.card.raised{box-shadow:0 6px 18px rgba(0,0,0,.18)}
.card h3{font-size:21px;font-weight:700;margin:14px 0 12px}
.card p{font-size:14px;line-height:24px;color:var(--text);padding:0 24px}
/* mission */
.mission{left:0;top:1983px;width:1200px;height:493px;background:linear-gradient(180deg,#3b4a2a 0%,#4d6a2a 35%,#5a7f2b 70%,#486a22 100%)}
.mission-shade{left:0;top:1983px;width:1200px;height:493px;background:rgba(0,0,0,.28)}
.mission-title{left:0;top:2082px;width:1200px;text-align:center;font-size:40px;font-weight:700;color:var(--white)}
.mission-text{left:250px;top:2168px;width:700px;text-align:center;font-size:20px;font-weight:500;line-height:36px;color:var(--white)}
.mission-btns{left:460px;top:2322px;display:flex;gap:18px}
.mission-btns .btn{height:42px;font-size:14px;padding:0 22px}
/* social */
.social-title{left:0;top:2580px;width:1200px;text-align:center;font-size:40px;font-weight:700}
.feed{top:2686px;width:229px;display:flex;flex-direction:column;gap:8px}
.post{border:1px solid #ddd;background:var(--white);padding:10px;text-align:center}
.post .photo{height:168px;margin-bottom:8px}
.post.image-only .photo{height:168px;margin:0}
.post p{font-size:13px;line-height:19px;color:#333}
.avatar{position:relative;width:38px;height:38px;border-radius:50%;background:#a68a6c;margin:10px auto 6px}
.avatar span{position:absolute;right:-5px;top:-3px;width:15px;height:15px;border-radius:50%;border:2px solid var(--white)}
.post h4{font-size:16px;font-weight:700;color:var(--green)}
.post small{display:block;font-size:12px;color:#666;margin-top:3px}
.load-more{left:520px;top:3330px;height:47px;font-size:14px;padding:0 28px}
/* footer */
.footer{left:0;top:3493px;width:1200px;height:446px;background:var(--footer);color:var(--white)}
.f-head{font-size:17px;font-weight:700;text-transform:uppercase}
.f-head::after{content:"";display:block;width:56px;height:3px;background:var(--green);margin-top:10px}
.links{list-style:none;margin-top:26px;font-size:14px;line-height:27px}
.links li::before{content:"» ";color:#ccc}
.contact-row{display:flex;gap:34px;align-items:flex-start;font-size:14px;line-height:22px;margin-bottom:18px}
.f-divider{width:1px;height:250px;background:#333}
.email-box{width:254px;height:34px;border:1px solid #777;font-size:12px;padding:10px 8px;margin-top:18px}
.subscribe{margin-top:14px;height:32px;font-size:11px;padding:0 22px;border-radius:16px}
.copy-line{left:110px;top:3857px;width:980px;height:1px;background:#333}
.copy{left:110px;top:3886px;font-size:15px}
.socials{left:955px;top:3880px;display:flex;gap:6px}
.socials span{width:28px;height:28px;border-radius:50%;border:1.5px solid #ccc}
</style>
</head>
<body>

<!-- HERO -->
<div class="abs hero-photo" role="img" aria-label="Cows and a horse grazing in a green pasture under a cloudy sky"></div>
<div class="abs brand">Cedar Hollow Farms</div>
<nav class="abs nav"><span>Home</span><span>Services</span><span>About Us</span><span>Animals</span><span>Contact Us</span></nav>
<span class="abs btn nav-donate">
  <svg width="18" height="18" viewBox="0 0 24 24" fill="none" stroke="#fff" stroke-width="2"><path d="M3 20h6l8-5M3 16h5l4-2h3"/><circle cx="16" cy="6" r="3"/></svg>Donate</span>
<h1 class="abs hero-title">Cedar Hollow Farms</h1>
<p class="abs hero-sub">Lorem ipsum dolor amet consectetur adipiscing eiusmod tempor incididunt ut labore dolore magna aliqua.</p>
<svg class="abs hero-curve" width="1200" height="150" viewBox="0 0 1200 150" preserveAspectRatio="none"><path d="M0 60 Q600 170 1200 30 L1200 150 L0 150 Z" fill="#fff"/></svg>

<div class="action" style="left:203px;top:578px"><div class="action-inner">
  <svg width="46" height="46" viewBox="0 0 24 24" fill="none" stroke="#fff" stroke-width="1.6"><ellipse cx="12" cy="16" rx="4.5" ry="3.5"/><circle cx="6" cy="10" r="2"/><circle cx="18" cy="10" r="2"/><circle cx="9.5" cy="5.5" r="2"/><circle cx="14.5" cy="5.5" r="2"/></svg>Adopt</div></div>
<div class="action" style="left:418px;top:578px"><div class="action-inner">
  <svg width="46" height="46" viewBox="0 0 24 24" fill="none" stroke="#fff" stroke-width="1.6"><path d="M12 10s-4-2.5-4-5a2 2 0 0 1 4-1 2 2 0 0 1 4 1c0 2.5-4 5-4 5z"/><path d="M2 15h5l4 2h5l5-4M2 20h7l7-1"/></svg>Care</div></div>
<div class="action" style="left:628px;top:578px"><div class="action-inner">
  <svg width="46" height="46" viewBox="0 0 24 24" fill="none" stroke="#fff" stroke-width="1.6"><circle cx="7" cy="9" r="2"/><circle cx="17" cy="9" r="2"/><circle cx="12" cy="7" r="2.3"/><path d="M3 19v-4a4 4 0 0 1 8 0M13 15a4 4 0 0 1 8 0v4M8 19v-5a4 4 0 0 1 8 0v5"/></svg>Volunteer</div></div>
<div class="action" style="left:844px;top:578px"><div class="action-inner">
  <svg width="46" height="46" viewBox="0 0 24 24" fill="none" stroke="#fff" stroke-width="1.6"><path d="M2 21h7l9-6M2 16h6l4-2h4"/><circle cx="15" cy="6" r="3.5"/></svg>Donate</div></div>

<!-- ABOUT -->
<h2 class="abs about-title">About Cedar Hollow</h2>
<div class="abs about-text">
  <p>Lorem ipsum dolor sit amet, consectetur adipiscing elit, sed do eiusmod tempor incididunt ut labore et dolore magna aliqua.</p>
  <p>Ut enim ad minim veniam, quis nostrud exercitation ullamco laboris nisi ut aliquip ex ea commodo consequat. Duis aute irure dolor in reprehenderit in voluptate velit esse cillum dolore eu fugiat nulla pariatur. Excepteur sint occaecat cupidatat non proident, sunt in culpa qui officia deserunt mollit anim id est laborum.</p>
</div>
<span class="abs btn about-btn">Read More
  <svg width="16" height="16" viewBox="0 0 16 16"><circle cx="8" cy="8" r="7" fill="#fff"/><path d="M6 4.5 9.5 8 6 11.5" fill="none" stroke="#3c9a1e" stroke-width="2"/></svg></span>
<div class="abs video-frame"></div>
<div class="abs video" role="img" aria-label="Video still of horses grazing behind a wooden fence among trees"></div>
<div class="abs play"><svg width="60" height="60" viewBox="0 0 60 60"><path d="M25 19 40 30 25 41Z" fill="#fff"/></svg></div>

<!-- HELP -->
<div class="abs help"></div>
<svg class="abs" style="left:0;top:1320px" width="1200" height="100" viewBox="0 0 1200 100" preserveAspectRatio="none"><path d="M0 0 L1200 0 L1200 20 Q600 110 0 20 Z" fill="#fff"/></svg>
<h2 class="abs help-title">The Best Way To Help</h2>
<div class="abs card" style="left:113px">
  <svg width="86" height="86" viewBox="0 0 48 48" fill="none" stroke="#3c9a1e" stroke-width="1.6"><circle cx="24" cy="8" r="3"/><path d="M24 2v1M18 8h1M29 8h1M20 4l1 1M28 4l-1 1"/><path d="M6 40h36M12 40v-8M24 40v-12M36 40v-8"/><path d="M12 32c-3 0-5-2-5-4 3 0 5 2 5 4zm0 0c3 0 5-2 5-4-3 0-5 2-5 4zM24 28c-3 0-5-2-5-4 3 0 5 2 5 4zm0 0c3 0 5-2 5-4-3 0-5 2-5 4zM36 32c-3 0-5-2-5-4 3 0 5 2 5 4zm0 0c3 0 5-2 5-4-3 0-5 2-5 4z"/></svg>
  <h3>Go Plant-Based</h3><p>Lorem ipsum dolor sit do amet, consectetur adipiscing elit, tempor do eiusmod tempor incididunt</p></div>
<div class="abs card raised" style="left:454px">
  <svg width="86" height="86" viewBox="0 0 48 48" fill="none" stroke="#3c9a1e" stroke-width="1.6"><ellipse cx="25" cy="16" rx="6" ry="5"/><circle cx="16" cy="9" r="2.5"/><circle cx="34" cy="9" r="2.5"/><circle cx="21" cy="4" r="2.2"/><circle cx="29" cy="4" r="2.2"/><path d="M4 30h8l8 4h10c2 0 2 3 0 3H20M12 44l18-2 14-10c2-2 0-4-2-3l-10 6"/></svg>
  <h3>Rescue &amp; Rehabilitate</h3><p>Lorem ipsum dolor sit do amet, consectetur adipiscing elit, tempor do eiusmod tempor incididunt</p></div>
<div class="abs card" style="left:793px">
  <svg width="86" height="86" viewBox="0 0 48 48" fill="none" stroke="#3c9a1e" stroke-width="1.6"><rect x="6" y="6" width="10" height="10"/><rect x="20" y="18" width="10" height="10"/><path d="M11 16v8h9M25 28v6h-8M30 23h6"/><circle cx="11" cy="38" r="4"/><path d="M38 32c-4 0-6-3-6-6a6 6 0 0 1 12 0c0 3-2 6-6 6zM38 32l-2 8M38 32l2 8"/><circle cx="38" cy="26" r="2"/></svg>
  <h3>Tour The Farm</h3><p>Lorem ipsum dolor sit do amet, consectetur adipiscing elit, tempor do eiusmod tempor incididunt</p></div>

<!-- MISSION -->
<div class="abs mission" role="img" aria-label="Herd of cattle grazing in an open field at the edge of a forest"></div>
<div class="abs mission-shade"></div>
<h2 class="abs mission-title">Our Mission</h2>
<p class="abs mission-text">Lorem ipsum dolor sit amet, consectetur adipiscing elit sed do eiusmod tempor incididunt ut labore magna aliqua. Ut enim ad minim veniam quis nostrud ea commodo consequat exercitation.</p>
<div class="abs mission-btns">
  <span class="btn"><svg width="18" height="18" viewBox="0 0 24 24" fill="none" stroke="#fff" stroke-width="2"><path d="M3 20h6l8-5M3 16h5l4-2h3"/><circle cx="16" cy="6" r="3"/></svg>Donate</span>
  <span class="btn"><svg width="18" height="18" viewBox="0 0 24 24" fill="none" stroke="#fff" stroke-width="2"><circle cx="8" cy="8" r="3"/><circle cx="16" cy="8" r="3"/><path d="M2 20a6 6 0 0 1 12 0M10 20a6 6 0 0 1 12 0"/></svg>Join Us</span>
</div>

<!-- SOCIAL FEEDS -->
<h2 class="abs social-title">Social Feeds</h2>
<div class="abs feed" style="left:113px">
  <div class="post"><div class="photo" role="img" aria-label="Volunteer kneeling beside a goat on hay" style="background:linear-gradient(180deg,#8aa35d,#b39a6a)"></div>
    <p>Lorem ipsum dolor sit amet, consectetur adipiscing elit, sed eiusmod tempor</p>
    <div class="avatar" role="img" aria-label="Profile photo"><span style="background:#3b5998"></span></div><h4>Tobin Reyes,</h4><small>@tobinreyes - Jan 30, 2018</small></div>
  <div class="post"><p>Lorem ipsum dolor sit amet, consectetur adipiscing elit, sed eiusmod tempor</p>
    <div class="avatar" role="img" aria-label="Profile photo"><span style="background:#1da1f2"></span></div><h4>Levi Brandt,</h4><small>@levibrandt - Jan 03, 2018</small></div>
</div>
<div class="abs feed" style="left:360px">
  <div class="post"><p>Lorem ipsum dolor sit amet, consectetur adipiscing elit, sed eiusmod tempor</p>
    <div class="avatar" role="img" aria-label="Profile photo"><span style="background:#1da1f2"></span></div><h4>Marla Quint,</h4><small>@marlaquint - Jan 23, 2018</small></div>
  <div class="post image-only"><div class="photo" role="img" aria-label="Black and white cows standing in a meadow" style="background:linear-gradient(180deg,#7aa048,#5f8a34)"></div></div>
  <div class="post"><p>Lorem ipsum dolor sit amet, consectetur adipiscing elit, sed eiusmod tempor</p>
    <div class="avatar" role="img" aria-label="Profile photo"><span style="background:#e4405f"></span></div><h4>Nora Vale,</h4><small>@noravale - Jan 08, 2018</small></div>
</div>
<div class="abs feed" style="left:609px">
  <div class="post image-only"><div class="photo" role="img" aria-label="Pony standing in a grassy paddock" style="background:linear-gradient(180deg,#9ab66a,#6c9a33)"></div></div>
  <div class="post"><p>Lorem ipsum dolor sit amet, consectetur adipiscing elit, sed eiusmod tempor</p>
    <div class="avatar" role="img" aria-label="Profile photo"><span style="background:#e4405f"></span></div><h4>Anya Holt,</h4><small>@anyaholt - Jan 20, 2018</small></div>
  <div class="post image-only"><div class="photo" role="img" aria-label="White goats grazing on green grass" style="background:linear-gradient(180deg,#86b04c,#cfd5c6)"></div></div>
</div>
<div class="abs feed" style="left:859px">
  <div class="post"><p>Lorem ipsum dolor sit amet, consectetur adipiscing elit, sed eiusmod tempor</p>
    <div class="avatar" role="img" aria-label="Profile photo"><span style="background:#1da1f2"></span></div><h4>Tobin Reyes,</h4><small>@tobinreyes - Dec 30, 2018</small></div>
  <div class="post image-only"><div class="photo" role="img" aria-label="Herd of cows in a wide pasture" style="background:linear-gradient(180deg,#a9b9a2,#6f9a3a)"></div></div>
  <div class="post"><p>Lorem ipsum dolor sit amet, consectetur adipiscing elit, sed eiusmod tempor</p>
    <div class="avatar" role="img" aria-label="Profile photo"><span style="background:#3b5998"></span></div><h4>Ezra Pike,</h4><small>@ezrapike - Dec 28, 2018</small></div>
</div>
<span class="abs btn load-more"><svg width="14" height="14" viewBox="0 0 16 16" fill="none" stroke="#fff" stroke-width="2"><path d="M13 8a5 5 0 1 1-2-4M11 1v3h3"/></svg>Load More</span>

<!-- FOOTER -->
<footer class="abs footer">
  <div class="abs" style="left:110px;top:72px">
    <div class="f-head">Quick Links</div>
    <ul class="links"><li>Home</li><li>About Us</li><li>Services</li><li>Our Animals</li><li>Events</li><li>Get Involved</li></ul>
  </div>
  <div class="abs f-divider" style="left:312px;top:72px"></div>
  <div class="abs" style="left:407px;top:72px">
    <div class="f-head">Contact Details</div>
    <div style="margin-top:38px">
      <div class="contact-row"><svg width="16" height="18" viewBox="0 0 24 24" fill="none" stroke="#aaa" stroke-width="2"><path d="M12 22s7-7 7-12a7 7 0 0 0-14 0c0 5 7 12 7 12z"/><circle cx="12" cy="10" r="2.5"/></svg><span>123A, Sample Street, Sample City,<br>New State, PO 1234</span></div>
      <div class="contact-row"><svg width="16" height="16" viewBox="0 0 24 24" fill="#aaa"><path d="M6 2h4l2 5-3 2a12 12 0 0 0 6 6l2-3 5 2v4a2 2 0 0 1-2 2A18 18 0 0 1 4 4a2 2 0 0 1 2-2z"/></svg><span>(+1) 123 456 7890</span></div>
      <div class="contact-row"><svg width="16" height="14" viewBox="0 0 24 20" fill="none" stroke="#aaa" stroke-width="2"><rect x="2" y="2" width="20" height="16"/><path d="M2 3l10 8 10-8"/></svg><span>hello@cedarhollowfarms.com</span></div>
    </div>
  </div>
  <div class="abs f-divider" style="left:740px;top:72px"></div>
  <div class="abs" style="left:832px;top:72px;width:260px">
    <div class="f-head">Newsletter Subscription</div>
    <p style="font-size:14px;line-height:24px;margin-top:30px">Register your Email Address to get More Information about us</p>
    <div class="email-box">Email Address</div>
    <span class="btn subscribe">Subscribe</span>
  </div>
</footer>
<div class="abs copy-line"></div>
<div class="abs copy" style="color:#fff">Copyrights © 2019 Cedar Hollow Farms.  All Rights Reserved.</div>
<div class="abs socials"><span></span><span></span><span></span><span></span></div>

</body>
</html>
```